Elegant Business Card for Technology Company

Client is a supplier of innovative industrial communications and automation equipment since 2002. This contest is to gather fresh ideas for a redesign of the existing business card. Client is looking for design that best communicates tagline "Industrial Networking and Computing Specialist".

Design submissions should look modern, clean, elegant and professional. It should not be cluttered. Use white as the primary colour. Orange and black as secondary colour. Refer to jpeg File 1 on the current design.

Fonts used by Client used include Arial Regular, Arial Black, Roboto Regular, Roboto Black and Lato.

The winning design will be sent for offset printing using super white 250gsm artcard paper (open for suggestions).

Target Market(s)

System Engineers, Project Managers, Purchasing Managers from companies providing engineering services for Smart Cities.

Industry/Entity Type

Information Technology

Contact Information for Business Card

Refer to PDF File 3 for Business Card Details. Priority of short contact information would be as follows Name > Job Title > Email > Mobile > Web > Tel > Fax > Business Address >UEN (UEN represents company registration number)

Font styles to use
Sans Serif

Colors
ffffff
f37122
000000
5c5c5c

Requirements
Must have
• Refer to AI File 2 (Company Logo) & PDF File 3 (Information on Namecard)
Should not have
• No QR codes
• No Social Media Icons
• Do not create full Black or Orange colour background

```html
<!DOCTYPE html>
<html lang="en">
<head>
<meta charset="utf-8">
<title>ORLINK Business Card</title>
<link href="https://fonts.googleapis.com/css2?family=Roboto:wght@400;500;900&display=swap" rel="stylesheet">
<style>
  :root {
    --white: #ffffff;
    --orange: #f37122;
    --orange-deep: #c9561a;
    --black: #000000;
    --ink: #111111;
    --grey: #5c5c5c;
    --logo-grey: #2b2b2b;
    --stage: #e9e7e4;
  }
  * { margin: 0; padding: 0; box-sizing: border-box; }
  html, body { width: 1200px; height: 950px; overflow: hidden; }
  body {
    background: var(--stage);
    font-family: "Roboto", Arial, sans-serif;
    position: relative;
  }
  .card {
    position: absolute;
    left: 250px;
    width: 700px;
    height: 400px;
    overflow: hidden;
    box-shadow: 0 6px 18px rgba(0,0,0,0.18);
  }

  /* Back side */
  .card-back {
    top: 50px;
    background: linear-gradient(120deg, var(--white) 0%, #f4f4f4 55%, #d9d9d9 100%);
  }
  .brand {
    display: flex;
    align-items: center;
    gap: 14px;
  }
  .brand-dot {
    border-radius: 50%;
    background: var(--orange);
    flex: none;
  }
  .brand-name {
    font-family: "Roboto", Arial, sans-serif;
    font-weight: 900;
    color: var(--logo-grey);
    letter-spacing: 2px;
    line-height: 1;
  }
  .card-back .brand { position: absolute; left: 150px; top: 70px; }
  .card-back .brand-dot { width: 66px; height: 66px; }
  .card-back .brand-name { font-size: 76px; }
  .tagline {
    position: absolute;
    left: 300px;
    top: 200px;
    color: var(--grey);
    font-size: 17px;
    line-height: 1.45;
    letter-spacing: 0.3px;
  }

  /* Front side */
  .card-front {
    top: 500px;
    background: linear-gradient(100deg, var(--orange-deep) 0%, var(--orange) 60%, #f58a45 100%);
  }
  .front-dark {
    position: absolute;
    left: 0; top: 0;
    width: 430px; height: 400px;
    background: var(--ink);
  }
  .front-disc {
    position: absolute;
    left: 255px; top: 30px;
    width: 370px; height: 370px;
    border-radius: 50%;
    background: radial-gradient(circle at 42% 38%, var(--white) 0%, #f7f7f7 55%, #e4e4e4 100%);
    box-shadow: -4px 4px 14px rgba(0,0,0,0.25);
  }
  .card-front .brand { position: absolute; left: 318px; top: 175px; }
  .card-front .brand-dot { width: 56px; height: 56px; }
  .card-front .brand-name { font-size: 62px; }

  .contact {
    position: absolute;
    left: 40px; top: 36px;
    color: var(--white);
  }
  .person-name {
    color: var(--orange);
    font-size: 20px;
    font-weight: 500;
    letter-spacing: 1px;
  }
  .person-title {
    font-size: 15px;
    letter-spacing: 0.8px;
    margin-top: 2px;
  }
  .address {
    font-style: normal;
    font-size: 15px;
    line-height: 1.3;
    margin-top: 24px;
    margin-left: 10px;
  }
  .details {
    list-style: none;
    margin-top: 22px;
    font-size: 15px;
    line-height: 1.35;
  }
  .details li { display: flex; align-items: center; gap: 8px; }
  .details svg { width: 13px; height: 13px; flex: none; fill: var(--orange); }
</style>
</head>
<body>

<section class="card card-back" aria-label="Card back">
  <div class="brand">
    <span class="brand-dot"></span>
    <span class="brand-name">ORLINK</span>
  </div>
  <p class="tagline">
    Industrial Networking &amp; Computing Specialist<br>
    Ethernet / Wireless / Cellular<br>
    Routing / Serial / Fieldbus Connectivity<br>
    Remote Automation
  </p>
</section>

<section class="card card-front" aria-label="Card front">
  <div class="front-dark"></div>
  <div class="front-disc"></div>
  <div class="brand">
    <span class="brand-dot"></span>
    <span class="brand-name">ORLINK</span>
  </div>

  <div class="contact">
    <h1 class="person-name">DANIEL KOH</h1>
    <p class="person-title">SALES MANAGER</p>
    <address class="address">
      25 Kallang Way<br>
      Block 7 #02-15<br>
      (Suite B)<br>
      Singapore 349512
    </address>
    <ul class="details">
      <li><svg viewBox="0 0 16 16"><path d="M3 1h3l1 4-2 1a9 9 0 0 0 5 5l1-2 4 1v3c0 1-1 2-2 2A13 13 0 0 1 1 3c0-1 1-2 2-2z"/></svg>+65 6123 4501</li>
      <li><svg viewBox="0 0 16 16"><path d="M4 0h8a1 1 0 0 1 1 1v14a1 1 0 0 1-1 1H4a1 1 0 0 1-1-1V1a1 1 0 0 1 1-1zm1 2v10h6V2zm3 11a1 1 0 1 0 0 2 1 1 0 0 0 0-2z"/></svg>+65 9123 4567</li>
      <li><svg viewBox="0 0 16 16"><path d="M4 1h8v4H4zM1 6h14v7h-3v2H4v-2H1zm4 5v3h6v-3z"/></svg>+65 6123 4502</li>
      <li><svg viewBox="0 0 16 16"><path d="M1 3h14v10H1zm1 1v1l6 4 6-4V4z"/></svg>sales@orlink.com.sg</li>
      <li><svg viewBox="0 0 16 16"><path d="M8 1a7 7 0 1 0 0 14A7 7 0 0 0 8 1zm0 2a5 5 0 0 1 0 10A5 5 0 0 1 8 3zm-1 2v2H5v2h2v2h2V9h2V7H9V5z"/></svg>www.orlink.com.sg</li>
    </ul>
  </div>
</section>

</body>
</html>
```